Tradlo - Forex Signal Services Moments Matter Most. Reshape your path.

I need an attractive eye catching web design that is azure friendly. I currently have a web programmer working on the backend of my website. Now I need a professional design to attract and retain customers. This site needs to be mobile friendly.

Tradlo is a highly reputable, trustworthy and professional site that offers forex signals to traders in all parts of the globe. With accurate and reliable forex signals, traders can not only make money but also boost their profits.

At Tradlo, we want our clients to have complete faith on us and our services! We also do not want our users to lead a simple and monotonous life. Instead our goal is to help them create an extra source of steady income. However, this is possible only when our clients resolve to change their lives for the better. They need to change their mindset and most importantly develop a positive frame of mind. That’s exactly why at Tradlo, we provide our clients with innumerable personal development tools and resources that’ll aid them in changing all the aspects of their lives. We want our traders to feel inspired and educate them in the right way!

Colors are flexible.

I do like the simplicity of www.brightmarkvo.example.
I do want a design more professional in appearance and not everything on page one.

I have not been able to decide on a logo. There is one of lower quality as I have not paid for it yet but I will if you decide it's the best for my business I will. Or should one feel that they have a better idea for a logo, I will pay for it if i like it.

I have included some of the content of my site so you can get a feel for where I am coming from.
(Please note that this content is still in the editing process)
Updates

Project Deadline Extended Reason: My content was not complete nor finalization of the final logo. We will allow a few more days for designers to modify the website.Thank you for your patience and understanding. Added Tuesday, January 24, 2017

Target Market(s)

I work with Forex Traders, Investors wanting to control their own portfolios, and remote nomads/mellienials

Coding

Coded - Design and coding required

Number of Pages Required

5+ page

Requirements
Must have
• I must have a professional clean look. I want the site to be interactive and eye catching. I want my audience hooked within seconds of opening it. It has to have all important information first. Photos must be legit and not spammy. I work as a representative in the financial market. I want my site to reflect that I stand by my product and reputation means everything to me. This site has to be engaging.
• Sorry, I should have included this earlier of what I will all need on this site.
• I'll have about Tradlo (my company, what we stand for, who we work with, my strategy, etc....
• about me (why i started this company, who I am)
• Performance (graphs and recent posts of signals)
• Membership (how to sign up)
• Terms of service/legal/disclaimers
• FAQS
• Personal Development Resources
• Forex Education Resources
Nice to have
• Quick links to bounce around the site faster.
Should not have
• I do not want over the top white collar conservative.

```html
<!DOCTYPE html>
<html lang="en">
<head>
<meta charset="utf-8">
<title>Tradlo - Forex Signal Services</title>
<link rel="stylesheet" href="https://fonts.googleapis.com/css2?family=Open+Sans:wght@400;600;700&family=Questrial&display=swap">
<style>
:root{
  --red:#d8262d;
  --ink:#1e1e1e;
  --text:#555;
  --muted:#777;
  --white:#fff;
  --soft:#f2f2f2;
  --note:#ebebeb;
  --foot:#262626;
  --social:#2a6cb4;
  --line:#d6d6d6;
}
*{margin:0;padding:0;box-sizing:border-box}
html,body{width:1200px;height:3442px;overflow:hidden}
body{font-family:"Open Sans",Arial,sans-serif;color:var(--text);background:var(--white)}
.wrap{width:940px;margin:0 auto;position:relative}
h2{font-family:"Questrial","Century Gothic",sans-serif;font-weight:400;color:var(--red);text-align:center;font-size:27px;line-height:1.2}

/* header */
.site-header{height:154px;position:relative}
.brand{position:absolute;left:131px;top:40px;display:flex;align-items:center;gap:10px}
.brand-dot{width:26px;height:26px;border-radius:50%;background:var(--red)}
.brand-name{font-family:"Questrial",sans-serif;font-size:34px;color:#333}
.social{display:flex;gap:9px}
.social span{width:24px;height:24px;border-radius:50%;background:var(--social);display:block}
.site-header .social{position:absolute;left:978px;top:34px}
.main-nav{position:absolute;right:130px;top:94px;display:flex;gap:36px;font-size:14px;color:#333}

/* hero */
.hero{height:461px;position:relative;background:
  radial-gradient(ellipse at 35% 40%,#3f5fa8 0%,#1d2e5c 35%,transparent 60%),
  radial-gradient(ellipse at 78% 45%,#5a2c3a 0%,#26202f 40%,transparent 65%),
  linear-gradient(180deg,#3a3d48 0%,#1a1c24 55%,#0d0e12 100%)}
.hero-text{position:absolute;left:0;right:0;top:340px;text-align:center;color:var(--white);text-transform:uppercase}
.hero-text span{display:inline-block;background:rgba(0,0,0,.72);font-family:"Open Sans",sans-serif;font-weight:700;letter-spacing:1px}
.hero-kicker{font-size:22px;padding:4px 14px;margin-bottom:10px}
.hero-title{font-size:23px;padding:4px 16px}

/* welcome */
.welcome{height:292px;padding-top:72px;text-align:center}
.welcome p{font-size:13.5px;line-height:21px;margin-top:16px}
.welcome .lead{font-size:17px;line-height:29px;color:#333;margin-top:14px}

/* strategy */
.strategy{height:397px;position:relative;color:var(--white);text-align:center;background:
  radial-gradient(ellipse at 85% 55%,#3a2020 0%,transparent 45%),
  linear-gradient(90deg,#0e1a2a 0%,#13263d 45%,#1d2636 75%,#2a2225 100%)}
.strategy .wrap{padding-top:52px}
.strategy h2{color:var(--white)}
.strategy p{font-size:12px;line-height:18px;margin-top:10px}
.strategy .lead{font-size:17px;line-height:25px}
.btn-light{display:inline-block;margin-top:18px;background:var(--white);color:#111;font-size:12px;font-weight:700;padding:8px 14px;text-transform:uppercase}

/* why us */
.why{height:784px;padding-top:74px;text-align:center}
.why .intro{font-size:13.5px;line-height:21px;margin-top:12px}
.why-row{display:flex;gap:24px;margin-top:34px;text-align:left}
.why-photo{width:333px;height:291px;flex:none;background:linear-gradient(160deg,#9ec4ea 0%,#3f78b8 45%,#123a6e 100%)}
.why-list{list-style:none;font-size:11px;color:#333;padding-top:2px}
.why-list li{height:36px;padding-left:16px;position:relative;line-height:16px;white-space:nowrap}
.why-list li:before{content:"•";position:absolute;left:0}
.why .body{font-size:13px;line-height:21px;margin-top:34px}
.why .lead{font-size:17px;line-height:26px;color:#333;margin-top:20px}
.why .close{font-size:13px;line-height:21px;margin-top:22px}

/* who we serve */
.serve{height:723px;background:var(--soft);padding-top:74px}
.serve .sub{text-align:center;font-family:"Questrial",sans-serif;font-size:18px;color:#444;margin-top:12px}
.cards{display:grid;grid-template-columns:450px 450px;gap:37px 36px;margin-top:26px}
.card{display:flex;background:var(--white);height:219px}
.card-img{width:223px;flex:none}
.card-body{padding:24px 16px 0 16px}
.card h3{font-family:"Questrial",sans-serif;font-weight:400;font-size:22px;color:#222;line-height:1.25}
.card p{font-size:11px;line-height:16px;color:#666;margin-top:18px}
.btn-line{display:inline-block;margin-top:14px;border:1px solid var(--line);font-size:10px;color:#888;padding:7px 18px}
.img-traders{background:linear-gradient(150deg,#6b6f78 0%,#2e3340 55%,#11141b 100%)}
.img-investors{background:linear-gradient(135deg,#f1c7dc 0%,#d68fb8 45%,#a34f84 100%)}
.img-nomads{background:linear-gradient(180deg,#2f6cb0 0%,#4c8bc9 55%,#1c2a3e 100%)}
.img-home{background:linear-gradient(150deg,#eef0f2 0%,#c9cdd2 50%,#8b8580 100%)}

/* what we do */
.offer{height:306px;padding-top:74px}
.steps{display:flex;margin-top:32px}
.step{width:250px}
.step:nth-child(2){width:248px}
.step:nth-child(3){width:261px}
.step svg{display:block;height:26px}
.step h4{font-family:"Questrial",sans-serif;font-weight:400;font-size:20px;color:#222;line-height:26px;margin-top:12px}

/* disclaimer */
.disclaimer{height:211px;background:var(--note);padding-top:42px}
.disclaimer p{font-size:10.5px;line-height:20px;color:#555}

/* footer */
.site-footer{height:114px;background:var(--foot);color:#cfcfcf;font-size:11px}
.site-footer .wrap{padding-top:34px}
.foot-links{display:flex;gap:10px}
.copy{margin-top:14px}
.site-footer .social{position:absolute;right:0;top:45px}
</style>
</head>
<body>

<header class="site-header">
  <div class="brand"><span class="brand-dot"></span><span class="brand-name">Tradlo</span></div>
  <div class="social" aria-label="Social links"><span></span><span></span><span></span></div>
  <nav class="main-nav"><span>Home</span><span>Why Us?</span><span>How it works?</span><span>Contact</span></nav>
</header>

<section class="hero" role="img" aria-label="Trader watching forex charts on several monitors">
  <div class="hero-text">
    <span class="hero-kicker">Forex Signal Services</span><br>
    <span class="hero-title">Moments Matter Most. Reshape Your Path</span>
  </div>
</section>

<section class="welcome">
  <div class="wrap">
    <h2>Welcome To Tradlo.com!</h2>
    <p>We use proven strategies to help traders in succeeding in the forex market. Our forex experts provide high-probability, professional and consistent forex signals and charts that help traders in maximizing their profits and eliminating losses.</p>
    <p class="lead">Try our free Currency Education service to find out what differentiates us from our competitors and how we can aid you in becoming a professional trader!</p>
  </div>
</section>

<section class="strategy" role="img" aria-label="Stock ticker screen with glowing price numbers">
  <div class="wrap">
    <h2>Our Strategy</h2>
    <p>Tradlo.com works with both day as well as intraday traders. We only hold a maximum of one position at any given point in time. Once we’ve placed an order we do not move SL or TP targets.</p>
    <p>We follow naked forex trading techniques including price action, immediate trend and personalized mathematical formulas.</p>
    <p class="lead">Our success stems from our strict enforcement of discipline, patience, attitude, economics and timing to help our traders maximize their gains from forex trading.</p>
    <p>At Tradlo, we trade GBP/USD, EUR/USD, AUD/USD, USD/CHF and USD/JPY pairs only and target anywhere between 25-50 pips a day with a risk/reward ratio of at least 2:1. Our maximum drawdown is 18% and we strive to average 150-250 pips per month. We strongly recommend no more than 3% leveraged risk of your account for any trade. Most trades are closed within hours.</p>
    <span class="btn-light">Click here to learn more about forex basics!</span>
  </div>
</section>

<section class="why">
  <div class="wrap">
    <h2>Why Us?</h2>
    <p class="intro">Put simply, because we’re different! We are a ‘Never before Seen’ forex trading company that is focused on guiding, mentoring and assisting traders in every possible manner! We provide tools, resources and technology that allow traders to fulfill their trading aspirations and achieve success.</p>
    <div class="why-row">
      <div class="why-photo" role="img" aria-label="Glass office towers seen from below against a blue sky"></div>
      <ul class="why-list">
        <li>We offer speedy, consistent, accurate and desired results.</li>
        <li>We’re a highly dependable and trusted forex trading platform.</li>
        <li>Our motto is to ‘Change Your World’ and also to ensure that you earn profits on a regular basis.</li>
        <li>Our objective is to provide global access to trusted forex signals.</li>
        <li>Our services are highly affordable.</li>
        <li>We offer High Probable forex strategies with high rewards.</li>
        <li>We set transparent entry price and exit levels.</li>
        <li>Our team will constantly update you regarding the status of your trade till the time it is closed.</li>
      </ul>
    </div>
    <p class="body">We trade four days a weekonly Tuesday to Friday (no le only trade 4 days a week Tuesday to Friday)and daily signals are sent to traders only if they meet our requisite rules and regulations. Pending order signals are generally issued by around 8:30 EST time. Click here for local time zone* Our signals are sent via push notification on our app Available AppHarbor Store and PlayDeck*, Chirper, and Snapgram accounts. Traders can also receive our forex signals by SMS and email.</p>
    <p class="lead">At Tradlo.com, we aspire to become one of the most reputable and fastest growing forex signal service providing platform to traders around the world!</p>
    <p class="close">If you’re tired of your 9-5 job or need an alternate source of income, then don’t look any further! We’ll help you in acquiring a consistent income and a building a bright future through forex trading.</p>
  </div>
</section>

<section class="serve">
  <div class="wrap">
    <h2>HOW WILL FOREX SIGNALS HELP YOU?</h2>
    <p class="sub">Who do we serve?</p>
    <div class="cards">
      <article class="card">
        <div class="card-img img-traders" role="img" aria-label="Businessman touching a rising chart on a screen"></div>
        <div class="card-body"><h3>Forex Traders</h3><p>A Forex signal service is provided for those who are struggling to make money on the forex market.</p><span class="btn-line">Read more</span></div>
      </article>
      <article class="card">
        <div class="card-img img-investors" role="img" aria-label="Banknotes and savings paperwork"></div>
        <div class="card-body"><h3>Investors and Retirees</h3><p>If you are someone that has been tricked before or have lost your savings to investment companies and would</p><span class="btn-line">Read more</span></div>
      </article>
      <article class="card">
        <div class="card-img img-nomads" role="img" aria-label="Person relaxing at a laptop by the sea"></div>
        <div class="card-body"><h3>Remote Nomads</h3><p>People that just want to live their lives the way they chose and be able to make the funds to pay for their travels</p><span class="btn-line">Read more</span></div>
      </article>
      <article class="card">
        <div class="card-img img-home" role="img" aria-label="Man working on a laptop at home"></div>
        <div class="card-body"><h3>Work from home</h3><p>Work At Home has become popular as the internet becomes available to more and more homes around the world</p><span class="btn-line">Read more</span></div>
      </article>
    </div>
  </div>
</section>

<section class="offer">
  <div class="wrap">
    <h2>What we do for you</h2>
    <div class="steps">
      <div class="step">
        <svg width="30" height="26" viewBox="0 0 30 26" aria-hidden="true"><g fill="#222"><rect x="0" y="1" width="5" height="5"/><rect x="8" y="1" width="22" height="5"/><rect x="0" y="10.5" width="5" height="5"/><rect x="8" y="10.5" width="22" height="5"/><rect x="0" y="20" width="5" height="5"/><rect x="8" y="20" width="22" height="5"/></g></svg>
        <h4>Choose the best<br>forex pair</h4>
      </div>
      <div class="step">
        <svg width="32" height="26" viewBox="0 0 32 26" aria-hidden="true"><g fill="#222"><rect x="0" y="0" width="2.5" height="26"/><rect x="0" y="23.5" width="32" height="2.5"/><rect x="6" y="12" width="4" height="10"/><rect x="13" y="6" width="4" height="16"/><rect x="20" y="14" width="4" height="8"/><rect x="27" y="3" width="4" height="19"/></g></svg>
        <h4>Analyze the forex<br>chart</h4>
      </div>
      <div class="step">
        <svg width="30" height="26" viewBox="0 0 30 26" aria-hidden="true"><rect x="0" y="3" width="30" height="21" fill="#222"/><path d="M1 4 L15 15 L29 4" fill="none" stroke="#fff" stroke-width="2"/></svg>
        <h4>Send Forex Signals</h4>
      </div>
      <div class="step">
        <svg width="34" height="26" viewBox="0 0 34 26" aria-hidden="true"><rect x="1.5" y="4" width="31" height="18" fill="none" stroke="#222" stroke-width="3"/><circle cx="17" cy="13" r="5" fill="#222"/></svg>
        <h4>&nbsp;You &nbsp;make Money</h4>
      </div>
    </div>
  </div>
</section>

<section class="disclaimer">
  <div class="wrap">
    <p>Disclaimer : Trading foreign exchange (“Forex”) on margin carries a high level of risk, and may not be suitable for all investors. Before deciding to trade Forex you should carefully consider your investment objectives, level of experience, and only trade with the money you are prepared to lose. The possibility exists that you could sustain a loss in excess of all of your deposited funds and therefore you should not speculate with capital that you cannot afford to lose. You should be aware of all the risks associated with foreign exchange. Clients must be at least 18 years old to use the services of TRADLO. You acknowledge that past performance is not an indicator of future returns and that references to performance on this Site are provided as historical benchmarks only. TRADLO does not take responsibility for loss incurred as a result of our trading signals. By signing up as a member you acknowledge that we are not providing financial advice and that you are making the decision to use our trades on your own account. All information provided by TRADLO, in any form, is for educational purposes only.</p>
  </div>
</section>

<footer class="site-footer">
  <div class="wrap">
    <div class="foot-links"><span>Home</span><span>|</span><span>Why Us?</span><span>|</span><span>How it works?</span><span>|</span><span>Contact</span></div>
    <p class="copy">Copyright © 2017 Company name. All rights reserved.</p>
    <div class="social" aria-label="Social links"><span></span><span></span><span></span></div>
  </div>
</footer>

</body>
</html>
```